Website Design for Landscaping/Concrete Company

I need a website that is informative about what my company does and also offers before and after pictures of completed work. I already have a logo. The website must say "FREE ESTIMATES" somewhere and list a phone number. I would like to stick with the logo colors or similar (black and lime green).
Services Offered by Tomlet Builders:
Landscaping
Mowing
Concrete
Sidewalks
Brush Removal
Land Beautification

Please list the company name in large letters TOMLET BUILDERS
and also the contact information in large font.

Right now I am looking for a somewhat coverpage for my website. I don't have a lot of information for people to point and click on yet. Id like to get a coverpage to get my name out and then have a designer come back in a few months and update with more pictures and information.
Updates

If allowed please submit projects after due date. I made a mistake and only posted for one day. Thanks.

Coding

Coded - Design and coding required

```html
<!DOCTYPE html>
<html lang="en">
<head>
<meta charset="utf-8">
<title>Tomlet Builders – Landscaping &amp; Concrete</title>
<link href="https://fonts.googleapis.com/css2?family=Poppins:wght@300;400;500;600;700;800&display=swap" rel="stylesheet">
<style>
:root{
  --lime:#8dbb0f;
  --lime-bright:#a8d400;
  --lime-soft:#eef7d4;
  --ink:#222222;
  --text:#6b6b6b;
  --cream:#f8f7f2;
  --footer:#2b2b2b;
  --footer-dark:#1f1f1f;
  --white:#ffffff;
}
*{margin:0;padding:0;box-sizing:border-box}
html,body{width:1200px;height:3917px;overflow:hidden}
body{font-family:'Poppins',sans-serif;color:var(--ink);background:var(--white);position:relative}
.abs{position:absolute}
.photo{position:absolute}

/* hero */
.hero{position:absolute;left:0;top:0;width:1200px;height:672px;
  background:linear-gradient(160deg,#2f3a17 0%,#4f6a22 40%,#6b8a2e 70%,#3c4d18 100%)}
.topbar{position:absolute;left:0;top:0;width:1200px;height:24px;background:#000}
.navline{position:absolute;left:0;top:144px;width:1200px;height:1px;background:rgba(255,255,255,.2)}
.brand{position:absolute;left:38px;top:82px;display:flex;align-items:center;gap:8px;
  color:var(--lime-bright);font-weight:700;font-size:14px;letter-spacing:.5px;line-height:1.1}
.brand-mark{width:16px;height:16px;background:var(--lime-bright)}
.nav{position:absolute;top:90px;left:338px;display:flex;gap:0}
.nav a{color:#fff;text-decoration:none;font-weight:600;font-size:14px;margin-right:49px}
.cta{position:absolute;left:830px;top:76px;width:160px;height:40px;border-radius:20px;background:var(--lime);
  color:#fff;font-size:11.5px;font-weight:700;display:flex;align-items:center;justify-content:center;letter-spacing:.3px}
.phone{position:absolute;left:1015px;top:84px;color:#fff;font-weight:600;font-size:19px;display:flex;align-items:center;gap:10px}
.welcome{position:absolute;left:0;top:282px;width:1200px;text-align:center}
.welcome .small{color:#fff;font-weight:300;font-size:44px;line-height:1.1}
.welcome .big{color:var(--lime-bright);font-weight:700;font-size:46px;line-height:1.15}

/* service card */
.services{position:absolute;left:38px;top:540px;width:1124px;height:315px;background:#fff;
  box-shadow:0 6px 20px rgba(0,0,0,.12);display:flex}
.service{flex:1;text-align:center;padding-top:50px;position:relative}
.service+.service::before{content:"";position:absolute;left:0;top:60px;height:185px;width:1px;background:#d8d8d8}
.service .icon{width:62px;height:54px;margin:0 auto;border:2px solid var(--lime);border-radius:8px;background:var(--lime-soft)}
.service h3{font-size:21px;font-weight:500;margin:16px 0 10px}
.service p{font-size:13px;color:var(--text);line-height:21px;width:200px;margin:0 auto}
.service .more{display:inline-block;margin-top:18px;font-size:10px;font-weight:600;color:var(--lime);text-decoration:underline}
.arrow-btn{position:absolute;width:46px;height:46px;border-radius:50%;background:#fff;box-shadow:0 2px 8px rgba(0,0,0,.15);
  display:flex;align-items:center;justify-content:center}

/* who we are */
.section-title{font-size:28px;font-weight:700;color:var(--ink)}
.section-title span{color:var(--lime)}
.about{position:absolute;left:107px;top:955px;width:440px}
.about p{font-size:13.5px;color:var(--text);line-height:21px;margin-top:22px}
.about .more{display:inline-block;margin-top:22px;font-size:10px;font-weight:600;color:var(--lime);text-decoration:underline}

/* works */
.works{position:absolute;left:0;top:1388px;width:1200px;height:779px;background:var(--cream)}
.works h2{position:absolute;top:60px;width:1200px;text-align:center}
.filters{position:absolute;top:126px;left:0;width:1200px;display:flex;justify-content:center;gap:52px;font-size:10.5px;font-weight:600}
.filters .active{color:var(--lime);border-bottom:2px solid var(--lime);padding:0 10px 8px}
.tile{position:absolute;width:265px;height:241px}

/* estimation */
.estimate{position:absolute;left:0;top:2167px;width:1200px;height:596px;
  background:linear-gradient(180deg,#2d3a1c 0%,#3f5621 45%,#4f7a1d 100%)}
.estimate h2{position:absolute;top:60px;width:1200px;text-align:center;color:#fff;font-size:27px;font-weight:700}
.field{position:absolute;background:rgba(133,178,10,.82);border:1px solid rgba(255,255,255,.35);color:#fff;
  font-size:12px;font-weight:600;padding:18px 0 0 18px}
.submit{position:absolute;left:500px;top:491px;width:209px;height:47px;background:#fff;color:var(--lime);
  font-size:11.5px;font-weight:700;display:flex;align-items:center;justify-content:center}

/* testimonial */
.quote{position:absolute;left:620px;top:2940px;width:520px}
.quote h2{font-size:32px;font-weight:700;line-height:40px}
.quote p{font-size:14px;color:var(--text);line-height:26px;margin-top:30px}
.quote .who{color:var(--lime);font-size:14px;margin-top:20px}

/* footer */
.footer{position:absolute;left:0;top:3397px;width:1200px;height:427px;background:var(--footer);color:#fff}
.footer h4{font-size:20px;font-weight:600}
.footer ul{list-style:none;font-size:14px;line-height:35px}
.footer .contact{position:absolute;left:74px;top:163px;font-size:14px;font-weight:600;line-height:26px}
.footer .emails{position:absolute;left:71px;top:302px;font-size:14px;color:var(--lime-bright);line-height:26px}
.social{position:absolute;left:988px;top:238px;display:flex;gap:24px}
.social span{width:18px;height:18px;border-radius:50%;background:#777}
.social span:first-child{background:var(--lime-bright)}
.copy{position:absolute;left:0;top:3824px;width:1200px;height:93px;background:var(--footer-dark);
  color:#bbb;font-size:12px;display:flex;align-items:center;justify-content:center}
</style>
</head>
<body>

<header class="hero" role="img" aria-label="Photo of a gardener in orange working in a lush garden"></header>
<div class="topbar"></div>
<div class="navline"></div>
<div class="brand"><span class="brand-mark"></span><span>TOMLET<br>BUILDERS</span></div>
<nav class="nav"><a>HOME</a><a>ABOUT</a><a>SERVICES</a><a>NEWS</a><a>CONTACT</a></nav>
<div class="cta">FREE ESTIMATION</div>
<div class="phone">
  <svg width="16" height="16" viewBox="0 0 24 24"><path fill="#8dbb0f" d="M6.6 10.8a15 15 0 0 0 6.6 6.6l2.2-2.2c.3-.3.7-.4 1-.2 1.1.4 2.3.6 3.6.6.6 0 1 .4 1 1V20c0 .6-.4 1-1 1A17 17 0 0 1 3 4c0-.6.4-1 1-1h3.5c.6 0 1 .4 1 1 0 1.3.2 2.5.6 3.6.1.3 0 .7-.2 1z"/></svg>
  1800-555-0147
</div>
<div class="welcome"><div class="small">WELCOME TO</div><div class="big">TOMLET BUILDERS</div></div>

<section class="services">
  <div class="service"><div class="icon" role="img" aria-label="Trees icon"></div><h3>Landscaping</h3><p>Lorem ipsum dolor sit amet, consectetur adipiscing elit, sed do eiusmod tempor incididunt ut labore et dolore</p><span class="more">READMORE</span></div>
  <div class="service"><div class="icon" role="img" aria-label="Lawn mower icon"></div><h3>Mowing</h3><p>Lorem ipsum dolor sit amet, consectetur adipiscing elit, sed do eiusmod tempor incididunt ut labore et dolore</p><span class="more">READMORE</span></div>
  <div class="service"><div class="icon" role="img" aria-label="Concrete mixer truck icon"></div><h3>Concrete</h3><p>Lorem ipsum dolor sit amet, consectetur adipiscing elit, sed do eiusmod tempor incididunt ut labore et dolore</p><span class="more">READMORE</span></div>
  <div class="service"><div class="icon" role="img" aria-label="Pine trees icon"></div><h3>Sidewalks</h3><p>Lorem ipsum dolor sit amet, consectetur adipiscing elit, sed do eiusmod tempor incididunt ut labore et dolore</p><span class="more">READMORE</span></div>
</section>
<div class="arrow-btn" style="left:14px;top:650px"><svg width="12" height="12" viewBox="0 0 12 12"><path d="M8 1 3 6l5 5" stroke="#8dbb0f" stroke-width="2.4" fill="none"/></svg></div>
<div class="arrow-btn" style="left:1140px;top:655px"><svg width="12" height="12" viewBox="0 0 12 12"><path d="m4 1 5 5-5 5" stroke="#8dbb0f" stroke-width="2.4" fill="none"/></svg></div>

<section class="about">
  <h2 class="section-title">Who <span>We Are</span></h2>
  <p>Lorem ipsum dolor sit amet, consectetur adipiscing elit, sed do eiusmod tempor incididunt ut labore et dolore magna aliqua. Quis ipsum suspendisse ultrices gravida. Risus commodo viverra maecenas accumsan lacus vel facilisis.</p>
  <p>Lorem ipsum dolor sit amet, consectetur adipiscing elit, sed do eiusmod tempor incididunt ut labore et dolore magna aliqua. Quis ipsum suspendisse ultrices gravida. Risus commodo viverra maecenas accumsan lacus vel facilisis.</p>
  <span class="more">READMORE</span>
</section>
<div class="photo" style="left:630px;top:944px;width:451px;height:341px;background:linear-gradient(135deg,#6f8f22,#3f6a1a 60%,#8aa83a)" role="img" aria-label="Photo of a gardener trimming hedges"></div>

<section class="works">
  <h2 class="section-title">Our <span>Works</span></h2>
  <div class="filters"><span class="active">ALL</span><span>LANDSCAPING</span><span>MOWING</span><span>CONCRETE</span><span>SIDEWALKS</span><span>BRUSH REMOVAL</span><span>LAND BEAUTIFICATION</span></div>
</section>
<div class="tile" style="left:38px;top:1581px;background:linear-gradient(135deg,#4d7a1d,#8fb53a 60%,#c9a24a)" role="img" aria-label="Stone garden path photo"></div>
<div class="tile" style="left:324px;top:1581px;background:linear-gradient(160deg,#5e8f24,#7fb336)" role="img" aria-label="Lawn mower on grass photo"></div>
<div class="tile" style="left:611px;top:1581px;background:linear-gradient(135deg,#b9a58b,#8d7d68 60%,#d9a35a)" role="img" aria-label="Workers pouring concrete photo"></div>
<div class="tile" style="left:897px;top:1581px;background:linear-gradient(170deg,#8fb0c9,#c4c9c6 40%,#6d9c2c)" role="img" aria-label="Curved sidewalk photo"></div>
<div class="tile" style="left:38px;top:1843px;background:linear-gradient(135deg,#3f6a1c,#7aa33a)" role="img" aria-label="Worker trimming brush photo"></div>
<div class="tile" style="left:324px;top:1843px;background:linear-gradient(135deg,#6f9a2d,#4a7a20 60%,#b34a2c)" role="img" aria-label="Gardener planting flowers photo"></div>
<div class="tile" style="left:611px;top:1843px;background:linear-gradient(135deg,#c4b16a,#8ca13c)" role="img" aria-label="Mowing in sunlight photo"></div>
<div class="tile" style="left:897px;top:1843px;background:linear-gradient(135deg,#5a3a2c,#8c6a9a 50%,#4d6a3a)" role="img" aria-label="Colourful paved walkway photo"></div>

<section class="estimate" role="img" aria-label="Photo of a garden path with lawn, darkened">
  <h2>Free Estimation</h2>
  <div class="field" style="left:309px;top:134px;width:279px;height:53px">First Name</div>
  <div class="field" style="left:610px;top:134px;width:280px;height:53px">Last Name</div>
  <div class="field" style="left:309px;top:211px;width:581px;height:52px">Email Address</div>
  <div class="field" style="left:309px;top:283px;width:581px;height:51px">Phone Number</div>
  <div class="field" style="left:309px;top:360px;width:581px;height:96px">Message</div>
  <div class="submit">GET ESTIMATION</div>
</section>

<svg class="abs" style="left:40px;top:2850px" width="540" height="480" viewBox="0 0 540 480">
  <path d="M130 30C250 -10 380 40 430 90 560 210 470 400 300 440 150 470 60 390 80 220 90 130 80 50 130 30Z" fill="#eef7d4"/>
  <circle cx="60" cy="240" r="50" fill="#f0f0f0"/>
</svg>
<div class="photo" style="left:99px;top:2880px;width:440px;height:435px;border-radius:40% 55% 45% 50% / 35% 45% 55% 60%;background:linear-gradient(135deg,#5d8a26,#8fbf3a 50%,#c7b06c)" role="img" aria-label="Terraced flower garden with stone walls"></div>
<div class="abs" style="left:57px;top:3056px;width:86px;height:86px;border-radius:50%;background:var(--lime);display:flex;align-items:center;justify-content:center">
  <svg width="26" height="20" viewBox="0 0 26 20"><path d="M0 20V10C0 4 4 0 10 0v4c-3 0-5 2-5 5h5v11zM14 20V10c0-6 4-10 10-10v4c-3 0-5 2-5 5h5v11z" fill="#fff"/></svg>
</div>
<section class="quote">
  <h2>What Our Clients are Saying</h2>
  <p>This is due to their excellent service, competitive pricing and customer support. It's throughly refresing to get such a personal touch. Duis aute irure dolor in reprehenderit in voluptate velit esse cillum dolore eu fugiat nulla pariatur.</p>
  <div class="who">Dana Whitlow</div>
</section>
<svg class="abs" style="left:1060px;top:3300px" width="70" height="20" viewBox="0 0 70 20"><path d="M30 10H4m7-7-7 7 7 7" stroke="#3a8fd0" stroke-width="2" fill="none"/><path d="M40 10h26m-7-7 7 7-7 7" stroke="#cfcfcf" stroke-width="2" fill="none"/></svg>

<footer class="footer">
  <div class="brand" style="left:78px;top:80px"><span class="brand-mark"></span><span>TOMLET<br>BUILDERS</span></div>
  <div class="contact">Address line 1<br>Address line 2<br>Location<br>Mobile Number</div>
  <div class="emails">Email address line 1<br>Email address line 2</div>
  <div class="abs" style="left:468px;top:80px"><h4>Quick Links</h4><ul style="margin-top:18px"><li>Home</li><li>About us</li><li>Services</li><li>Blog</li><li>Contact us</li></ul></div>
  <div class="abs" style="left:706px;top:80px"><h4>Our Services</h4><ul style="margin-top:22px"><li>Landscaping</li><li>Mowing</li><li>Concrete</li><li>Sidewalks</li><li>Brush Removal</li><li>Land Beautification</li></ul></div>
  <div class="social"><span></span><span></span><span></span><span></span></div>
</footer>
<div class="copy">Copyright © 2021 TOMLET - All Rights Reserved.</div>

</body>
</html>
```